Fine Art business needs new website

We need a simple website with a home page, about us page, New sculptures, Sold sculptures, and a contact us page.Our sculptures are very high end one of a kind pieces. As such we need the site to be VERY elegant and professional. Lastly, because I'll be updating pictures on the website on a monthly basis it needs to be user friendly to update (Wordpress is preferred). The only branding we have so far for the business is a business card.
Updates
I wasn't completely ready when this project launched, also I am on the road right now and haven't been able to be as responsive to all you designers as I would like. I will work on giving feedback to all the top designs we've received so far. Thank you all so much for your participation and hardwork.
Target Market(s)
High end customers (affluent), art collectors, interior decorators/designers
Industry/Entity Type
Art Gallery
Coding
Coded - Design and coding required
Number of Pages Required
5+ page
Requirements
Must have
- Easily editable picture gallery for myself so that I can add new pieces(pictures of the pieces), remove sold pieces, etc. I would like the website to be built in wordpress so I can update it. I currently use mangewordpress through Netmarro for my other business website and would like to do the same for this one.
- Pages:
- -Intro page with featured pieces
- -Current pieces gallery (for sale) mainly a picture gallery
- -Sculptures archive (sold pieces) another picture gallery
- -About us: Pull-down of -about the artist (attached content)
- -Artistic Process (attached content)
- -Show Schedule:
- -one page dedicated to "friends of TMV" (basically a link page)
- TO BE CLEAR "www.pineroverslane.com" IS A TOTALLY DIFFERENT SITE AND I'M NOT TRYING TO COMBINE THE TWO OR JOIN THEM INTO ONE. This page needs be more elegant and seperate from the Pine Rovers site.
- UPDATE: I'd like a link to the TMV Faceplume page: https://www.faceplume-social.com/mirelcraftworks/
Nice to have
- I would like the pictures on the gallery pages able to have text connected with them (Materials, price)
- I would like the site style and fonts to be similar to our business cards we've already had designed (picture attached).
Should not have
- Too much flash or other things that will make the site slow to load.

```html
<!DOCTYPE html>
<html lang="en">
<head>
<meta charset="utf-8">
<title>Contact Us – TMV</title>
<link href="https://fonts.googleapis.com/css2?family=Lato:wght@400;700&display=swap" rel="stylesheet">
<style>
:root{
  --ink:#222222;
  --bar:#212121;
  --page:#f3f3f3;
  --white:#ffffff;
  --accent:#6b5fb5;
  --field-line:#b9b9b9;
  --rule:#dddddd;
}
*{box-sizing:border-box;margin:0;padding:0}
html,body{width:1200px;height:995px;overflow:hidden}
body{font-family:'Lato',sans-serif;background:var(--page);color:var(--ink);position:relative}
.site-header{position:absolute;left:0;top:0;width:1200px;height:74px;background:var(--bar);box-shadow:0 2px 6px rgba(0,0,0,.25)}
.main-nav{position:absolute;left:188px;top:22px;display:flex;gap:21px;font-size:15px;font-weight:700;color:var(--white);letter-spacing:.2px}
.main-nav a{color:inherit;text-decoration:none;display:flex;align-items:center;gap:6px}
.main-nav .is-current{position:relative}
.main-nav .is-current::after{content:"";position:absolute;left:2px;right:2px;top:23px;height:2px;background:var(--accent)}
.menu-toggle{position:absolute;left:976px;top:23px}
.contact-title{position:absolute;left:0;width:1200px;top:118px;text-align:center;font-size:28px;font-weight:700}
.title-rule{position:absolute;left:542px;top:162px;width:116px;height:1px;background:var(--rule)}
.intro{position:absolute;left:189px;top:198px;font-size:18.5px;letter-spacing:.3px}
.field-label{position:absolute;left:189px;font-size:17px;font-weight:700;letter-spacing:.3px}
.field-label span{font-weight:400;font-size:14px;vertical-align:top}
.field{position:absolute;left:189px;width:317px;height:34px;border:1px solid var(--field-line);background:var(--page)}
.field.is-focused{border-color:#333}
.caret{position:absolute;left:8px;top:9px;width:1px;height:16px;background:#666}
.field-area{width:557px;height:171px}
.send-btn{position:absolute;left:189px;top:681px;width:133px;height:51px;background:var(--bar);color:var(--white);border-radius:3px;display:flex;align-items:center;justify-content:center;font-weight:700;font-size:14.5px}
.site-footer{position:absolute;left:0;top:783px;width:1200px;height:212px;background:var(--bar);color:var(--white)}
.footer-heading{position:absolute;top:40px;font-size:22.5px;font-weight:700;letter-spacing:-.2px}
.footer-text{position:absolute;font-size:13px;line-height:21.4px}
.contact-line{display:flex;align-items:center;height:21.4px}
.contact-line svg{position:absolute;left:0}
.contact-list{position:absolute;left:526px;top:75px;width:240px;font-size:13px}
.contact-list .contact-line{padding-left:23px}
.contact-list strong{padding-left:23px;display:block;line-height:21.4px}
.social-links{position:absolute;right:189px;top:78px;display:flex;gap:9px;font-size:11px;font-weight:700}
</style>
</head>
<body>
<header class="site-header">
  <nav class="main-nav">
    <a>HOME</a>
    <a>ABOUT <svg width="11" height="7" viewBox="0 0 11 7"><path d="M1 1l4.5 4.5L10 1" fill="none" stroke="#fff" stroke-width="1.2"/></svg></a>
    <a>GALLERY</a>
    <a class="is-current">CONTACT</a>
  </nav>
  <svg class="menu-toggle" width="35" height="19" viewBox="0 0 35 19"><rect y="0" width="35" height="3" fill="#fff"/><rect y="8" width="35" height="3" fill="#fff"/><rect y="16" width="35" height="3" fill="#fff"/></svg>
</header>

<main>
  <h1 class="contact-title">CONTACT US</h1>
  <div class="title-rule"></div>
  <p class="intro">Any inquiries? Do drop us an email.</p>

  <label class="field-label" style="top:250px">NAME <span>*</span></label>
  <div class="field is-focused" style="top:276px"><div class="caret"></div></div>
  <label class="field-label" style="top:322px">EMAIL <span>*</span></label>
  <div class="field" style="top:348px"></div>
  <label class="field-label" style="top:394px">WEBSITE &nbsp;/ URL</label>
  <div class="field" style="top:420px"></div>
  <label class="field-label" style="top:466px">COMMENT OR MESSAGE<span>*</span></label>
  <div class="field field-area" style="top:492px"></div>
  <div class="send-btn">SEND</div>
</main>

<footer class="site-footer">
  <h2 class="footer-heading" style="left:197px">ABOUT US</h2>
  <p class="footer-text" style="left:196px;top:75px">This is a dummy text just<br>to provide text in the About Us<br>section which will be added correctly<br>later on.</p>

  <h2 class="footer-heading" style="left:526px">OUR ADDRESS</h2>
  <div class="contact-list">
    <div class="contact-line"><svg width="14" height="14" viewBox="0 0 14 14"><path d="M3 1l2.5 3-1.4 1.6c.8 1.7 2.2 3.1 3.9 3.9L9.6 8 13 10.5 11.6 13C6 12.6 1.4 8 1 2.4z" fill="#fff"/></svg>(555) 214-0398</div>
    <div class="contact-line"><svg width="16" height="12" viewBox="0 0 16 12"><rect x=".5" y=".5" width="15" height="11" fill="none" stroke="#fff"/><path d="M.5 .5l7.5 6 7.5-6M.5 11.5l5.5-5M15.5 11.5L10 6.5" fill="none" stroke="#fff"/></svg>hello@pinerovers.net</div>
    <div class="contact-line"><svg width="15" height="15" viewBox="0 0 15 15"><path d="M6 9L9 6M5 6.5L3 8.5a2.5 2.5 0 003.5 3.5l2-2M10 8.5l2-2A2.5 2.5 0 008.5 3l-2 2" fill="none" stroke="#fff" stroke-width="1.3"/></svg>www.mirelcraftworks.com</div>
    <strong>CONTACT US</strong>
  </div>

  <h2 class="footer-heading" style="right:189px">KEEP IN TOUCH</h2>
  <div class="social-links"><span>Chirpline</span><span>Pinmark</span><span>Faceplume</span><span>Snapframe</span></div>
</footer>
</body>
</html>
```